Electrictrian Contractor Website Design

We are working with an electrical contractor in California called Fennick Electric.

Some sites to use for content/competitors and inspiration:
https://corvanelectric.example
https://tralvenpage.example/web/contractor/ (lots of contractor website designs we've approved and continue to show clients)

Thank you for taking the time to consider designing a website for us. We are web developers based in Stockton, CA, USA. Most of our projects go through the same process. Understanding this process may help you win a project with us. We custom-code all of our websites in-house. We don’t have any requirements as to what tools you use for your design, but we prefer Figma files. For any design that we label as four-stars, we send it to the client for review. The client picks the final design they want us to use. Once we complete this process, we will continue to show additional clients all the four-star sites and purchase them later. Your designs will have multiple chances to sell. For better chances of success, we ask that you follow these guidelines.

IMAGES:
If you use any images or icons in the design, we ask that you have a link to the asset so we can purchase the image/icon. Most of the designs we submit do not have the customer’s images on them unless they have some great images. Be creative; show us the feeling you are trying to portray with your image choices. Use any royalty-free site you choose. We subscribe to Quorvane and mainly use their images, but we can purchase images outside of Quorvane.

PLEASE NOTE: we will not submit designs to clients with watermarks on the images.

FONTS:
We ask that you identify the fonts used in the design. This can be done in a message if you want. We typically use Pellmarsh Type and Quorvane Type.

CONTENT:
We're always open to different content and ideas. We often submit designs with stock images so the client can see our vision. We typically take pictures after the website launch to use their images with our vision. Lorem Ipsum is fine for paragraphs, but we ask that you write the headers in correct English. We want to be able to show the vision and identify the sections of the website.

INSPIRATION:
We typically add a couple of links in the brief of websites we like to help you get started in your design.

REVISIONS:
We do not often ask for revisions of the designs unless we see something in the design that may not appeal to the client. If there are slight changes that we want to make, we do that in the development process.

FEEDBACK:
We rarely give feedback on designs during the design process. We are working on many website projects and do not have the time to provide feedback. We usually respond if your request is well thought out and asks specific questions, but a note asking “feedback, please” usually goes unanswered

```html
<!DOCTYPE html>
<html lang="en">
<head>
<meta charset="utf-8">
<title>Fennick Electric – Electrical Contractor in California</title>
<link href="https://fonts.googleapis.com/css2?family=Montserrat:wght@400;500;600;700;800&family=Lato:wght@400;700&display=swap" rel="stylesheet">
<style>
:root{
  --navy:#0f3b7d;
  --navy-dark:#0b2f66;
  --yellow:#f5b800;
  --yellow-deep:#e9a600;
  --ink:#1b1b1b;
  --muted:#6a6a6a;
  --white:#ffffff;
  --paper:#f4f6f9;
}
*{margin:0;padding:0;box-sizing:border-box}
html,body{width:1200px;height:4563px;overflow:hidden}
body{position:relative;background:var(--white);font-family:'Lato',sans-serif;color:var(--ink)}
.abs{position:absolute}
.head{font-family:'Montserrat',sans-serif}

/* header */
.topbar{left:0;top:0;width:1200px;height:48px}
.topbar-info{top:12px;left:610px;display:flex;gap:46px;color:var(--white);font-family:'Montserrat',sans-serif;font-size:15px;font-weight:500;align-items:center}
.topbar-info span{display:flex;align-items:center;gap:14px}
.brand{left:110px;top:22px;width:230px;font-family:'Montserrat',sans-serif;font-weight:600;color:var(--navy);font-size:30px;line-height:36px;letter-spacing:5px;text-align:center}
.nav{top:76px;left:0;width:1200px;height:24px;font-family:'Montserrat',sans-serif;font-size:12px;font-weight:500;color:#222}
.nav a{position:absolute;color:inherit;text-decoration:none}
.nav .active{color:var(--navy);font-weight:700;text-decoration:underline}
.btn{display:flex;align-items:center;justify-content:center;gap:12px;background:var(--navy);color:var(--white);font-family:'Montserrat',sans-serif;font-weight:700;font-size:15px;text-transform:uppercase}
.btn.light{background:var(--white);color:var(--ink)}

/* hero */
.hero-photo{left:0;top:119px;width:1200px;height:673px;background:linear-gradient(100deg,#1f3f73 0%,#3a5b86 38%,#8a96a6 60%,#c8c2b4 78%,#d9b66b 100%)}
.hero-copy{left:110px;color:var(--white)}
.hero-welcome{top:252px;font-size:26px;font-weight:700;letter-spacing:1px}
.hero-title{top:292px;font-size:66px;letter-spacing:1px;white-space:nowrap}
.hero-title b{font-weight:800}
.hero-title span{font-weight:400}
.hero-state{top:386px;font-size:22px;font-weight:700;letter-spacing:5px}
.hero-lead{top:434px;width:486px;font-size:15px;line-height:26px;text-align:justify}
.dots{left:110px;top:622px;display:flex;gap:6px}
.dots i{width:11px;height:11px;border-radius:50%;background:#c8ccd3}
.dots i.on{background:var(--white)}

/* stats */
.stats{left:0;top:792px;width:1200px;height:268px;background:var(--yellow)}
.stat{top:8px;width:310px;text-align:center;font-family:'Montserrat',sans-serif}
.stat strong{display:block;font-size:54px;font-weight:600;line-height:64px}
.stat small{display:block;margin-top:14px;font-size:15px;font-weight:600}
.divider{top:8px;width:4px;height:100px;background:var(--navy-dark)}
.stats-note{top:168px;left:0;width:1200px;text-align:center;font-family:'Montserrat',sans-serif;font-size:19px;line-height:34px}

/* about */
.about-bg{left:0;top:1060px;width:1200px;height:571px;background:linear-gradient(180deg,#eef1f5 0%,#fff 25%,#fff 75%,#eef1f5 100%)}
.about-visual{left:130px;top:1160px;width:376px;height:376px;border-radius:50%;
  background:radial-gradient(circle at 38% 34%,#ffe07a 0%,#ffc928 30%,#f5b800 62%,#e39b00 100%);
  box-shadow:inset 0 0 0 14px rgba(255,255,255,.18),0 18px 40px rgba(233,166,0,.28)}
.about-visual::after{content:"";position:absolute;inset:88px;border-radius:50%;background:radial-gradient(circle at 45% 40%,#fff3c4 0%,#ffd24d 60%,#f2b000 100%);opacity:.55}
.section-title{font-family:'Montserrat',sans-serif;color:var(--navy);font-weight:400;text-transform:uppercase}
.section-title b{font-weight:700}
.about-copy{left:599px;top:1140px;width:494px;font-size:14px;line-height:27px;color:#333}
.about-copy h2{font-size:34px;margin-bottom:8px;line-height:42px}
.about-copy p{margin-bottom:14px}
.about-copy li{list-style:none;display:flex;gap:10px;align-items:flex-start;margin-bottom:6px}
.bolt{flex:none}

/* projects intro */
.intro{left:0;top:1700px;width:1200px;text-align:center}
.intro h2{font-size:35px;line-height:55px}
.intro p{margin-top:16px;color:var(--yellow);font-family:'Montserrat',sans-serif;font-weight:700;font-size:20px}

/* service rows */
.row{left:0;width:1200px;height:416px;border-top:2px solid var(--navy)}
.row-photo{top:0;height:414px}
.row-copy{width:450px;font-size:15px;line-height:30px;color:var(--muted)}
.row-copy h3{font-family:'Montserrat',sans-serif;font-size:26px;font-weight:600;color:var(--ink);margin-bottom:20px}
.row-copy p{margin-bottom:30px}
.row .btn{width:178px;height:50px}

/* testimonials */
.reviews{left:0;top:3563px;width:1200px;height:434px;border-top:2px solid var(--navy);background:linear-gradient(180deg,#eef1f5 0%,#fff 20%)}
.reviews h2{position:absolute;top:78px;width:100%;text-align:center;font-size:35px}
.card{top:195px;width:300px;height:195px;background:var(--white);border-radius:6px;box-shadow:0 4px 16px rgba(0,0,0,.12);text-align:center;padding-top:62px}
.avatar{position:absolute;left:116px;top:-34px;width:68px;height:68px;border-radius:50%;background:linear-gradient(#c9cdd4,#8d96a3);border:4px solid var(--white);box-shadow:0 2px 8px rgba(0,0,0,.2)}
.card h4{font-family:'Montserrat',sans-serif;font-size:16px;font-weight:700}
.stars{color:var(--yellow);font-size:11px;letter-spacing:2px;margin:6px 0 8px}
.card p{font-size:13px;line-height:26px;padding:0 20px;color:#333}
.arrow{top:260px;width:26px;height:26px;border-radius:50%;display:flex;align-items:center;justify-content:center}

/* footer */
.footer{left:0;top:3997px;width:1200px;height:507px}
.foot-brand{left:110px;top:4262px;width:276px;color:var(--white);font-family:'Montserrat',sans-serif;font-size:40px;line-height:48px;letter-spacing:8px;text-align:center;font-weight:400}
.socials{left:142px;top:4400px;display:flex;gap:24px}
.socials i{width:34px;height:34px;border-radius:50%;border:2px solid var(--white);display:block}
.socials i.on{background:var(--yellow);border-color:var(--yellow)}
.foot-col{top:4252px;color:var(--white);font-size:15px}
.foot-col h5{font-family:'Montserrat',sans-serif;font-size:21px;font-weight:700;margin-bottom:16px}
.foot-col li{list-style:none;line-height:35px}
.contact-line{display:flex;gap:16px;align-items:flex-start;margin-bottom:20px;line-height:22px}
.contact-line svg{flex:none}
.copyright{left:0;top:4504px;width:1200px;height:59px;background:var(--yellow);font-size:12px;font-weight:700;text-align:center;line-height:59px}
</style>
</head>
<body>

<!-- header -->
<svg class="abs topbar" viewBox="0 0 1200 48" aria-hidden="true"><polygon points="540,0 1200,0 1200,48 585,48" fill="var(--navy)"/></svg>
<div class="abs topbar-info">
  <span><svg width="16" height="16" viewBox="0 0 24 24"><path fill="#fff" d="M6.6 10.8a15 15 0 006.6 6.6l2.2-2.2c.3-.3.7-.4 1-.2 1.1.4 2.3.6 3.6.6.6 0 1 .4 1 1V20c0 .6-.4 1-1 1A17 17 0 013 4c0-.6.4-1 1-1h3.5c.6 0 1 .4 1 1 0 1.3.2 2.5.6 3.6.1.3 0 .7-.2 1z"/></svg>Call:+1 555 014 2290</span>
  <span><svg width="18" height="14" viewBox="0 0 24 18"><path fill="#fff" d="M2 0h20a2 2 0 012 2v1L12 10 0 3V2a2 2 0 012-2zm-2 5l12 7 12-7v11a2 2 0 01-2 2H2a2 2 0 01-2-2z"/></svg>Mail:info@fennickelectric.example</span>
</div>
<div class="abs brand">FENNICK<br>ELECTRIC</div>
<nav class="abs nav">
  <a class="active" style="left:431px">HOME</a>
  <a style="left:530px">ABOUT</a>
  <a style="left:631px">SERVICES</a>
  <a style="left:749px">PROJECT</a>
  <a style="left:863px">CAREERS</a>
</nav>
<div class="abs btn" style="left:957px;top:66px;width:138px;height:39px;font-size:13px;gap:8px">
  <svg class="bolt" width="14" height="22" viewBox="0 0 14 22"><polygon points="9,0 1,12 6,12 4,22 13,8 8,8" fill="var(--yellow)"/></svg>Contact Us</div>

<!-- hero -->
<div class="abs hero-photo" role="img" aria-label="Electrician in hard hat and safety vest testing a control panel with a multimeter"></div>
<svg class="abs" style="left:0;top:119px" width="1200" height="673" viewBox="0 0 1200 673" aria-hidden="true">
  <defs><linearGradient id="shade" x1="0" x2="1"><stop offset="0" stop-color="#0f3b7d" stop-opacity=".75"/><stop offset=".5" stop-color="#0f3b7d" stop-opacity="0"/></linearGradient></defs>
  <rect width="1200" height="673" fill="url(#shade)"/>
  <polygon points="0,673 550,608 585,528 1200,445 1200,673" fill="var(--yellow)"/>
</svg>
<div class="abs hero-copy head hero-welcome">WELCOME TO</div>
<div class="abs hero-copy head hero-title"><b>FENNICK</b> <span>ELECTRIC</span></div>
<div class="abs hero-copy head hero-state">IN CALIFORNIA</div>
<p class="abs hero-copy hero-lead">Lorem ipsum dolor sit amet, consectetur adipiscing elit, sed do eiusmod tempor incididunt ut labore et dolore magna aliqua.</p>
<div class="abs btn light" style="left:110px;top:518px;width:177px;height:49px">
  <svg class="bolt" width="20" height="36" viewBox="0 0 14 22"><polygon points="9,0 1,12 6,12 4,22 13,8 8,8" fill="var(--yellow)"/></svg>Get Started</div>
<div class="abs dots"><i></i><i></i><i class="on"></i><i></i></div>

<!-- stats -->
<section class="abs stats">
  <div class="abs stat" style="left:148px"><strong>2009</strong><small>YEAR OF FOUNDATION</small></div>
  <div class="abs divider" style="left:454px"></div>
  <div class="abs stat" style="left:458px"><strong>+3500</strong><small>FINALIZED PROJECTS</small></div>
  <div class="abs divider" style="left:767px"></div>
  <div class="abs stat" style="left:763px"><strong>+2100</strong><small>CAREER CLIENTS</small></div>
  <p class="abs stats-note">We have <b>10+ years</b> specializing in a vast variety of <b>Electrical and General Engineering</b><br>experience throughout <b>Northern California.</b></p>
</section>

<!-- about -->
<div class="abs about-bg"></div>
<div class="abs about-visual" role="img" aria-label="Round yellow graphic filled with a photograph of electrical wiring and panels"></div>
<div class="abs about-copy">
  <h2 class="section-title">About <b>Fennick</b> Electric</h2>
  <p>Lorem ipsum dolor sit amet, consectetur adipiscing elit, sed do eiusmod tempor incididunt ut labore et dolore magna aliqua. Ut enim ad minim nisi ut aliquip ex ea commodo consequat.</p>
  <p>Duis aute irure dolor in reprehenderit in voluptate velit esse cillum dolore eu fugiat nulla pariatur. Excepteur sint occaecat cupidatat non proident, sunt in culpa qui officia deserunt mollit anim id est laborum</p>
  <ul>
    <li><svg class="bolt" width="11" height="18" viewBox="0 0 14 22" style="margin-top:5px"><polygon points="9,0 1,12 6,12 4,22 13,8 8,8" fill="var(--yellow)"/></svg>Lorem ipsum dolor sit amet, consectetur adipiscing</li>
    <li><svg class="bolt" width="11" height="18" viewBox="0 0 14 22" style="margin-top:5px"><polygon points="9,0 1,12 6,12 4,22 13,8 8,8" fill="var(--yellow)"/></svg>Excepteur sint occaecat cupidatat non proident, sunt in culpa qui officia deserunt</li>
  </ul>
</div>
<div class="abs btn" style="left:599px;top:1494px;width:167px;height:50px">
  <svg class="bolt" width="20" height="36" viewBox="0 0 14 22"><polygon points="9,0 1,12 6,12 4,22 13,8 8,8" fill="var(--yellow)"/></svg>Read More</div>

<!-- intro -->
<div class="abs intro">
  <h2 class="section-title">Leave your next electrical and <b>general<br>engineering project</b></h2>
  <p>IN THE HANDS OF A CAPABLE AND TRUSTWORTHY TEAM!</p>
</div>

<!-- service rows -->
<section class="abs row" style="top:1898px">
  <div class="abs row-photo" style="left:603px;width:597px;clip-path:polygon(0 0,100% 0,100% 100%,101px 100%);background:linear-gradient(160deg,#9fb1c6,#d8cfbf 55%,#e7b46a)" role="img" aria-label="Two engineers in hard hats inspecting a power substation at sunset"></div>
  <svg class="abs" style="left:600px;top:0" width="110" height="414" aria-hidden="true"><line x1="3" y1="0" x2="104" y2="414" stroke="var(--navy)" stroke-width="2"/></svg>
  <div class="abs row-copy" style="left:110px;top:70px">
    <h3>Site Electrical Experience</h3>
    <p>Duis aute irure dolor in reprehenderit in voluptate velit esse cillum dolore eu fugiat nulla pariatur.</p>
    <p>Excepteur sint occaecat cupidatat non proident, sunt in culpa qui officia deserunt mollit anim id est laborum.</p>
  </div>
  <div class="abs btn" style="left:110px;top:292px"><svg class="bolt" width="20" height="36" viewBox="0 0 14 22"><polygon points="9,0 1,12 6,12 4,22 13,8 8,8" fill="var(--yellow)"/></svg>Learn More</div>
</section>

<section class="abs row" style="top:2313px">
  <div class="abs row-photo" style="left:0;width:599px;clip-path:polygon(0 0,502px 0,100% 100%,0 100%);background:linear-gradient(120deg,#3c5a78,#7d8f9c 50%,#c7d24a)" role="img" aria-label="Technician in hard hat checking a power distribution control screen"></div>
  <svg class="abs" style="left:498px;top:0" width="104" height="414" aria-hidden="true"><line x1="4" y1="0" x2="100" y2="414" stroke="var(--navy)" stroke-width="2"/></svg>
  <div class="abs row-copy" style="left:675px;top:80px">
    <h3>Power Distribution Experience</h3>
    <p>Duis aute irure dolor in reprehenderit in voluptate velit esse cillum dolore eu fugiat nulla pariatur.</p>
    <p>Excepteur sint occaecat cupidatat non proident, sunt in culpa qui officia deserunt mollit anim id est laborum.</p>
  </div>
  <div class="abs btn" style="left:675px;top:298px"><svg class="bolt" width="20" height="36" viewBox="0 0 14 22"><polygon points="9,0 1,12 6,12 4,22 13,8 8,8" fill="var(--yellow)"/></svg>Learn More</div>
</section>

<section class="abs row" style="top:2730px">
  <div class="abs row-photo" style="left:603px;width:597px;clip-path:polygon(0 0,100% 0,100% 100%,101px 100%);background:linear-gradient(130deg,#0e2246,#1d3f7a 55%,#c86a2a)" role="img" aria-label="Electrician in orange hard hat wiring a server and network cabinet"></div>
  <svg class="abs" style="left:600px;top:0" width="110" height="414" aria-hidden="true"><line x1="3" y1="0" x2="104" y2="414" stroke="var(--navy)" stroke-width="2"/></svg>
  <div class="abs row-copy" style="left:110px;top:70px">
    <h3>Lighting Experience</h3>
    <p>Duis aute irure dolor in reprehenderit in voluptate velit esse cillum dolore eu fugiat nulla pariatur.</p>
    <p>Excepteur sint occaecat cupidatat non proident, sunt in culpa qui officia deserunt mollit anim id est laborum.</p>
  </div>
  <div class="abs btn" style="left:110px;top:292px"><svg class="bolt" width="20" height="36" viewBox="0 0 14 22"><polygon points="9,0 1,12 6,12 4,22 13,8 8,8" fill="var(--yellow)"/></svg>Learn More</div>
</section>

<section class="abs row" style="top:3146px">
  <div class="abs row-photo" style="left:0;width:599px;clip-path:polygon(0 0,502px 0,100% 100%,0 100%);background:linear-gradient(120deg,#e9ecef,#c9ccd0 45%,#e08a3a)" role="img" aria-label="Electrician in white hard hat testing a breaker panel with a multimeter"></div>
  <svg class="abs" style="left:498px;top:0" width="104" height="414" aria-hidden="true"><line x1="4" y1="0" x2="100" y2="414" stroke="var(--navy)" stroke-width="2"/></svg>
  <div class="abs row-copy" style="left:675px;top:80px">
    <h3>Panel Experience</h3>
    <p>Duis aute irure dolor in reprehenderit in voluptate velit esse cillum dolore eu fugiat nulla pariatur.</p>
    <p>Excepteur sint occaecat cupidatat non proident, sunt in culpa qui officia deserunt mollit anim id est laborum.</p>
  </div>
  <div class="abs btn" style="left:675px;top:298px"><svg class="bolt" width="20" height="36" viewBox="0 0 14 22"><polygon points="9,0 1,12 6,12 4,22 13,8 8,8" fill="var(--yellow)"/></svg>Learn More</div>
</section>

<!-- testimonials -->
<section class="abs reviews">
  <h2 class="section-title">What <b>our customer says</b></h2>
  <div class="abs arrow" style="left:38px;background:#c5cad1"><svg width="10" height="12" viewBox="0 0 10 12"><polyline points="7,1 2,6 7,11" fill="none" stroke="#fff" stroke-width="2"/></svg></div>
  <div class="abs card" style="left:110px"><div class="avatar" role="img" aria-label="Customer portrait"></div><h4>Marlo Vessant</h4><div class="stars">★★★★★</div><p>Temporibus autem quibusdam et aut officiis debitis aut rerum necessitatibus saepe eveniet ut et voluptates</p></div>
  <div class="abs card" style="left:448px"><div class="avatar" role="img" aria-label="Customer portrait"></div><h4>Tobin Arkwell</h4><div class="stars">★★★★★</div><p>Itaque earum rerum hic tenetur a sapiente delectus, reiciendis voluptatibus maiores alias consequatur aut</p></div>
  <div class="abs card" style="left:787px"><div class="avatar" role="img" aria-label="Customer portrait"></div><h4>Elsa Brindle</h4><div class="stars">★★★★★</div><p>Nam libero tempore, cum soluta nobis est eligendi optio cumque nihil impedit quo minus id quod</p></div>
  <div class="abs arrow" style="left:1130px;background:var(--navy)"><svg width="10" height="12" viewBox="0 0 10 12"><polyline points="3,1 8,6 3,11" fill="none" stroke="#fff" stroke-width="2"/></svg></div>
</section>

<!-- footer -->
<svg class="abs footer" viewBox="0 0 1200 507" aria-hidden="true">
  <polygon points="0,0 500,52 560,108 1200,170 1200,507 0,507" fill="var(--yellow)"/>
  <polygon points="0,18 480,74 540,128 1200,242 1200,507 0,507" fill="var(--navy)"/>
</svg>
<div class="abs foot-brand">FENNICK<br>ELECTRIC</div>
<div class="abs socials" aria-label="Social links"><i class="on"></i><i></i><i></i><i></i></div>
<div class="abs foot-col" style="left:464px"><h5>QUICK LINK</h5><ul><li>Home</li><li>About</li><li>Services</li><li>Testimonials</li><li>Contact Us</li></ul></div>
<div class="abs foot-col" style="left:686px"><h5>HELP LINKS</h5><ul><li>FAQ</li><li>Terms of use</li><li>Privacy Policy</li><li>Support Links</li><li>Conditions</li></ul></div>
<div class="abs foot-col" style="left:896px">
  <h5>CONTACT US</h5>
  <div class="contact-line"><svg width="30" height="30" viewBox="0 0 30 30"><circle cx="15" cy="15" r="15" fill="#fff"/><path d="M15 7a5.5 5.5 0 00-5.5 5.5C9.5 17 15 23 15 23s5.5-6 5.5-10.5A5.5 5.5 0 0015 7zm0 7.5a2 2 0 110-4 2 2 0 010 4z" fill="var(--navy)"/></svg><span>Fennick Electric<br>United States</span></div>
  <div class="contact-line" style="align-items:center"><svg width="30" height="30" viewBox="0 0 30 30"><circle cx="15" cy="15" r="15" fill="#fff"/><path transform="translate(7 7) scale(.67)" fill="var(--navy)" d="M6.6 10.8a15 15 0 006.6 6.6l2.2-2.2c.3-.3.7-.4 1-.2 1.1.4 2.3.6 3.6.6.6 0 1 .4 1 1V20c0 .6-.4 1-1 1A17 17 0 013 4c0-.6.4-1 1-1h3.5c.6 0 1 .4 1 1 0 1.3.2 2.5.6 3.6.1.3 0 .7-.2 1z"/></svg><span>+1 555 014 2290</span></div>
  <div class="contact-line" style="align-items:center"><svg width="30" height="30" viewBox="0 0 30 30"><circle cx="15" cy="15" r="15" fill="#fff"/><path transform="translate(8 10) scale(.58)" fill="var(--navy)" d="M2 0h20a2 2 0 012 2v1L12 10 0 3V2a2 2 0 012-2zm-2 5l12 7 12-7v11a2 2 0 01-2 2H2a2 2 0 01-2-2z"/></svg><span>info@fennickelectric.example</span></div>
</div>
<div class="abs copyright">Copyrights@2024.Fennick Electric.All Rights Reserved</div>

</body>
</html>
```